Wordpress Theme for Harbourview Clinics

** Please view updated Sitemap2.pdf doc to clarify some confusion ***

This is a multiuser WordPress subscription site for Harbourview Clinics. Please see attachment for sitemap. Please do not include extra content like social media icons, search bars, or images. If you have questions, please ask for clarification.
The site contains the following pages and sub-pages:

1. Home
2. Our Clinic
2a. Our Clinic > Mission
2b. Our Clinic > Services
2c. Our Clinic > Clinic Policies
2d. Our Clinic > Schedules
3. Our Staff
3a. Our Staff > [Staff member page]
4. Resources
4a. Resources > Patient Health (index)
4b. Resources > Patient Health (index) > [post]
4c. Resources > Links
4d. Resources > Forms
5. Alerts
5a. Alerts > [Alert Page]
6. Contact Us

Includes the Following Pages, Subpages, and Content
1. Home
a. About Us
b. Our Staff
c. Bulletins
d. Accepting New Patients (shown as an alert widget)
e. Links
i. Physician Toolbox
ii. Book an Appointment
f. Clinic Policies
i. Show first 3 policies (e.g. Late Arrivals, Missed Appointments, Fees)
ii. Link to Clinic Policies page
g. Primary widget (displayed on all pages)
i. Hours of operation
ii. Contact Info
1. Tel
2. Fax
3. Email
4. Address
5. Get directions (link to Google Maps)
2. Our Clinic
a. Main Page
i. Clinic Name
ii. Overview
iii. Languages Spoken
iv. Secondary Navigation
1. Mission
2. Services
3. Clinic Policies
4. Schedules (see attachment)
b. Our Clinic > Mission
c. Our Clinic > Services
i. For each service include service TITLE and DESCRIPTION
d. Our Clinic > Clinic Policies
i. For each policy include policy TITLE and DESCRIPTION
ii. Include the following policies in mockup
1. Late arrivals
2. Missed appointments
3. Fees for missed appointments
4. Referrals and follow-ups
5. Services not covered by RDA
6. Information for LTF patients
7. Medical Legal Reports
e. Our Clinic > Schedules
3. Our Staff
a. Main Page
i. Display a list of staff members. Include NAME and DESIGNATION
b. Our Staff > [Staff Name]
i. Include NAME, PICTURE, DESIGNATION, and BIO
4. Resources
a. Resources > Patient Health
i. Main Page
1. Posts (ordered by date)
a. Title
b. Summary
2. Side Navigation
a. Post Categories
ii. Patient Health > [post title]
1. Title
2. Post Category
3. Date
4. Author
5. Summary
6. Body
b. Resources > Links
1. Secondary Navigation - Categories
a. Sample Categories:
i. Local Services
ii. RDA and Drug Coverage
iii. Mental Health Resources
2. Category page
a. Include the following links in the 'Local Services' category
i. Hypertension clinics
ii. Home Care services
iii. Vaccine Clinics
c. Resources > Forms
i. Display a table with form TITLE and CATEGORY
ii. Side Navigation
1. Form Categories
a. Use the following sample Categories
i. Referrals
ii. Insurance
iii. Intake
iv. Discharge
v. Waivers
5. Alerts
a. Main page
i. List of all Alert posts
1. Include post TITLE as a link to the post
ii. Side Navigation
1. Alerts Archive
a. shown as Month + Number of posts
iii. Alerts > [Alert page]
1. Include TITLE, DATE, AUTHOR, BODY
6. Contact Us
a. Map
b. Hours of operation
c. Address
d. Phone number
e. Fax number
e. Fax number
f. Map
g. Email

Design notes:
- fixed width
- responsive (need designs for mobile, tablet, and desktop)
- simple, dark font, white background
- use Font Awesome icons where needed
- user adds own logo

Target Market(s)

Harbourview Clinics

Industry/Entity Type

Medical

Number of Pages Required

5+ page

Font styles to use
Serif
Sans Serif

Requirements
Must have
• Please keep designs very simple.
• Examples:
• https://www.quolbin.com/install
• http://www.ventrohax.com/company/about-us
• http://brindlequota.org/
• http://www.trosk.com/
Should not have
• Minimal or no use of shadows and gradients

```html
<!DOCTYPE html>
<html lang="en">
<head>
<meta charset="utf-8">
<title>Resources | Harbourview Clinics</title>
<link href="https://fonts.googleapis.com/css2?family=Open+Sans:wght@400;600;700&display=swap" rel="stylesheet">
<style>
:root{
  --topbar:#0b8de2;
  --brand:#0a78c8;
  --ink:#1f1f1f;
  --text:#333;
  --muted-band:#f7f7f7;
  --card-bg:#f8f8f8;
  --card-line:#d4d4d4;
  --footer:#262626;
  --footer-text:#8a8a8a;
  --footer-head:#9a9a9a;
  --footer-rule:#3c3c3c;
  --white:#fff;
}
*{box-sizing:border-box;margin:0;padding:0}
html,body{width:1200px;height:788px;overflow:hidden}
body{font-family:"Open Sans",Arial,sans-serif;color:var(--text);background:var(--white);position:relative}
a{color:inherit;text-decoration:none}

.topbar{height:30px;background:var(--topbar);color:var(--white);font-size:9.5px;position:relative}
.topbar .help{position:absolute;left:161px;top:9px}
.topbar .help span+span{border-left:1px solid var(--white);margin-left:4px;padding-left:4px}
.topbar .links{position:absolute;right:161px;top:9px}
.topbar .links a+a{border-left:1px solid var(--white);margin-left:6px;padding-left:6px}

.header{height:82px;position:relative}
.brand{position:absolute;left:162px;top:27px;display:flex;align-items:center;gap:14px}
.brand-dot{width:28px;height:28px;border-radius:50%;background:var(--brand)}
.brand-name{font-size:20px;font-weight:600;color:var(--brand)}
.main-nav{position:absolute;left:555px;top:0;display:flex;height:83px}
.main-nav a{font-size:11px;color:var(--ink);display:flex;align-items:center;padding:0 16px;height:83px}
.main-nav a:nth-child(2){padding:0 22px 0 30px}
.main-nav a:nth-child(3){padding:0 18px 0 18px}
.main-nav a.active{background:var(--brand);color:var(--white);padding:0 6px;margin-left:17px;width:60px;justify-content:center}
.main-nav a:nth-child(5){padding:0 16px 0 34px}
.main-nav a:nth-child(6){padding:0 16px 0 22px}

.crumbs{height:60px;background:var(--muted-band);padding:16px 0 0 161px}
.crumbs h1{font-size:11px;font-weight:600;color:var(--ink);letter-spacing:.1px}
.crumbs p{font-size:10px;color:var(--ink);margin-top:6px;padding-left:1px}

.intro{position:absolute;left:160px;top:207px;width:520px}
.intro h2{font-size:13px;font-weight:600;color:var(--ink)}
.intro p{font-size:12.3px;line-height:18px;margin-top:10px;color:var(--text);padding-left:1px}

.cards{position:absolute;left:161px;top:351px;display:flex;gap:23px}
.card{width:277px;height:165px;border:1px solid var(--card-line);border-radius:3px;background:var(--card-bg);position:relative;text-align:center}
.card-band{height:53px;background:var(--brand);border-radius:2px 2px 0 0}
.card-badge{position:absolute;left:99px;top:-39px;width:78px;height:78px;border-radius:50%;background:var(--brand);border:3px solid var(--white);display:flex;align-items:center;justify-content:center}
.card h3{font-size:13.5px;font-weight:600;color:var(--ink);margin-top:13px;letter-spacing:.3px}
.card h3.current{color:var(--brand)}
.card p{font-size:9.6px;line-height:13.5px;color:var(--ink);margin:16px 12px 0}

.footer{position:absolute;left:0;top:561px;width:1200px;height:227px;background:var(--footer);border-top:3px solid var(--topbar)}
.footer-brand{position:absolute;left:162px;top:38px;display:flex;align-items:center;gap:14px}
.footer-brand .brand-dot{background:var(--white)}
.footer-brand .brand-name{color:var(--white)}
.footer-about{position:absolute;left:162px;top:87px;width:205px;font-size:8.6px;line-height:13.5px;color:#d0d0d0}
.fcol{position:absolute;top:34px}
.fcol h4{font-size:12px;font-weight:600;color:var(--footer-head);margin-bottom:10px}
.fcol li{list-style:none;font-size:9.5px;line-height:18px;color:var(--footer-text)}
.fcol li.on{color:#c8c8c8}
.nav-col{left:461px}
.links-col{left:686px}
.contact-col{left:836px}
.contact-col dl{display:grid;grid-template-columns:89px 120px;font-size:9.5px;line-height:15px;color:var(--footer-text);padding-left:2px}
.contact-col dd{padding-left:0}
.footer-bottom{position:absolute;left:0;top:188px;width:1200px;border-top:1px solid var(--footer-rule);height:36px;font-size:9.5px;color:var(--footer-text)}
.footer-bottom .copy{position:absolute;left:162px;top:12px}
.footer-bottom .legal{position:absolute;left:463px;top:12px;display:flex;gap:25px}
.footer-bottom .credit{position:absolute;right:164px;top:12px}
</style>
</head>
<body>

<div class="topbar">
  <div class="help"><span>To help Here : 222 333 4444</span><span>Email : Hello@ Harbourview.ca</span></div>
  <nav class="links"><a href="#">Book an Appointment</a><a href="#">Physician Toolbox</a></nav>
</div>

<header class="header">
  <a class="brand" href="#"><span class="brand-dot"></span><span class="brand-name">Harbourview Clinics</span></a>
  <nav class="main-nav">
    <a href="#">Home</a>
    <a href="#">Our Clinic</a>
    <a href="#">Our Staff</a>
    <a href="#" class="active">Resources</a>
    <a href="#">Alerts</a>
    <a href="#">Contact Us</a>
  </nav>
</header>

<section class="crumbs">
  <h1>RESOURCES LINKS</h1>
  <p>HOME / RESOURCES</p>
</section>

<section class="intro">
  <h2>RESOURCES</h2>
  <p>Lorem Ipsum is simply dummy text of the printing and typesetting industry. Lorem Ipsum has been the industry's standard dummy text ever since the 1500s,</p>
</section>

<section class="cards">
  <article class="card">
    <div class="card-band"></div>
    <div class="card-badge">
      <svg width="28" height="24" viewBox="0 0 28 24" aria-hidden="true"><rect x="9" y="1.5" width="10" height="5" rx="1.5" fill="none" stroke="#fff" stroke-width="2.2"/><rect x="1" y="6" width="26" height="17" rx="2.5" fill="#fff"/><rect x="5" y="6" width="1.6" height="17" fill="#0a78c8"/><rect x="21.4" y="6" width="1.6" height="17" fill="#0a78c8"/><rect x="12.3" y="9" width="3.4" height="11" fill="#0a78c8"/><rect x="8.5" y="12.8" width="11" height="3.4" fill="#0a78c8"/></svg>
    </div>
    <h3 class="current">PATIENT HEALTH</h3>
    <p>Lorem Ipsum is simply dummy text of the printing and typesetting industry. Lorem Ipsum has been the industry's standard dummy text ever since the 1500s,</p>
  </article>
  <article class="card">
    <div class="card-band"></div>
    <div class="card-badge">
      <svg width="28" height="28" viewBox="0 0 28 28" aria-hidden="true"><g fill="none" stroke="#fff" stroke-width="3.4" stroke-linecap="round"><rect x="3" y="4" width="10" height="14" rx="5" transform="rotate(-45 8 11)"/><rect x="15" y="10" width="10" height="14" rx="5" transform="rotate(-45 20 17)"/></g></svg>
    </div>
    <h3>RESOURCES LINKS</h3>
    <p>Lorem Ipsum is simply dummy text of the printing and typesetting industry. Lorem Ipsum has been the industry's standard dummy text ever since the 1500s,</p>
  </article>
  <article class="card">
    <div class="card-band"></div>
    <div class="card-badge">
      <svg width="22" height="28" viewBox="0 0 22 28" aria-hidden="true"><path d="M1 1h13l7 7v19H1z" fill="#fff"/><path d="M14 1v7h7" fill="#0a78c8" opacity=".35"/><g fill="#0a78c8"><rect x="5" y="12" width="12" height="2"/><rect x="5" y="16" width="12" height="2"/><rect x="5" y="20" width="12" height="2"/></g></svg>
    </div>
    <h3>RESOURCES FORMS</h3>
    <p>Lorem Ipsum is simply dummy text of the printing and typesetting industry. Lorem Ipsum has been the industry's standard dummy text ever since the 1500s,</p>
  </article>
</section>

<footer class="footer">
  <div class="footer-brand"><span class="brand-dot"></span><span class="brand-name">Harbourview Clinics</span></div>
  <p class="footer-about">Lorem Ipsum is simply dummy text of the printing and typesetting industry. Lorem Ipsum has been the industry's standard dummy text</p>

  <div class="fcol nav-col">
    <h4>Navigation</h4>
    <ul><li class="on">Home</li><li>Our Clinic</li><li>Newsletter</li><li>Our Staff</li><li>Resources</li></ul>
  </div>
  <div class="fcol links-col">
    <h4>Links</h4>
    <ul><li>Help</li><li>Support</li><li>Privacy Policy</li></ul>
  </div>
  <div class="fcol contact-col">
    <h4>Contact Us</h4>
    <dl>
      <dt>Telephone :</dt><dd>604-555-0187</dd>
      <dt>Email:</dt><dd>hello@harbourview.ca</dd>
      <dt>Address:</dt><dd>45 Alder Lane<br>&nbsp;Fernvale,B. Canada,<br>&nbsp;Q9Z 2XW</dd>
    </dl>
  </div>

  <div class="footer-bottom">
    <span class="copy">© 2015 Harbourview Clinics. All Rights Reservsd</span>
    <nav class="legal"><a href="#">About Us</a><a href="#">Terms of Use</a><a href="#">Privacy Policy</a></nav>
    <span class="credit">Site design &amp; developed by Pinegrove Web Studio</span>
  </div>
</footer>

</body>
</html>
```